Visitenkarten-Design für Steuerberater und Wirtschaftsprüfer
Thank you so much! Great communication, very fast and nice contact!
Zielgruppe
Steuerberater, Wirtschaftsprüfer in München
Aufgabenstellung
Wir haben ein Logo das uns gefällt, jetzt allerdings steht die Umfirmierung vor der Tür und aus der Kanzlei Zelliger (so unser Name) wird Zelliger und Partner mbB (die Jugend kommt mit als Partner in die Kanzlei) , Steuerberater, Wirtschaftsprüfer
Analog unseres alten Briefpapiers und der alten Visitenkarten soll eigentlich nur der Zusatz 'und Partner mbB' oder '& Partner mbB' gestaltet werden.
Das Dateiformat bei Visitenkarten bitte so übergeben, dass wir Namen selbst austauschen mit gängigen Officeprogrammen austauschen können. Bei den Visitenkarten ist das große 'Zelliger' geprägt.
Ich stelle das Logo, das aktuelle Briefpapier und aktuelle Visitenkarten ein. Unsere Farbe ist grau.
Das Logo bitte in .pdf, .png, .psd und .eps (sagt mi alles nichts, haben wir aber alles schon mal irgendwo gebraucht) , Visiten karten auch in .pddf und .ai
Bei Fragen kontaktiert mich gern jederzeit.

```html
<!DOCTYPE html>
<html lang="de">
<head>
<meta charset="utf-8">
<title>Zelliger &amp; Partner mbB – Visitenkarte</title>
<link rel="stylesheet" href="https://fonts.googleapis.com/css2?family=Jost:wght@300;400&display=swap">
<style>
  :root {
    --stage: #3b4149;
    --card: #58595b;
    --card-edge: #4c4d4f;
    --ink-light: #e4e4e4;
    --ink-muted: #a9a9ab;
    --emboss: #8c8c8e;
    --emboss-soft: #7a7a7c;
    --rule: #f2f2f2;
  }
  * { box-sizing: border-box; margin: 0; padding: 0; }
  html, body {
    width: 1200px; height: 900px; overflow: hidden;
    background: var(--stage);
    font-family: "Jost", "Helvetica Neue", Arial, sans-serif;
  }
  .stage { position: relative; width: 1200px; height: 900px; }
  .card {
    position: absolute; left: 290px; width: 620px; height: 401px;
    background: var(--card);
    box-shadow: 0 10px 24px rgba(0,0,0,.35);
    border: 1px solid var(--card-edge);
  }
  .card--back { top: 36px; }
  .card--front { top: 463px; }

  /* Wortmarke */
  .wordmark { position: absolute; font-weight: 300; line-height: 1; letter-spacing: .04em; }
  .wordmark__name { display: block; text-transform: uppercase; }
  .wordmark__suffix { display: block; text-transform: uppercase; }
  .wordmark__tagline { display: block; font-weight: 300; text-transform: uppercase; letter-spacing: .06em; }

  .card--back .wordmark { left: 150px; top: 118px; color: var(--emboss); }
  .card--back .wordmark__name { font-size: 76px; }
  .card--back .wordmark__suffix { font-size: 27px; margin-top: 2px; }
  .card--back .wordmark__tagline { font-size: 19px; color: var(--emboss-soft); margin-top: 8px; }

  .card--front .wordmark { left: 346px; top: 196px; color: var(--ink-light); }
  .card--front .wordmark__name { font-size: 44px; }
  .card--front .wordmark__suffix { font-size: 16px; margin-top: 1px; }
  .card--front .wordmark__tagline {
    font-size: 11px; color: var(--ink-muted); margin-top: 4px;
    padding-bottom: 3px; border-bottom: 1px solid var(--ink-muted);
  }

  .person { position: absolute; left: 56px; top: 44px; color: var(--ink-light); }
  .person__name { font-size: 27px; font-weight: 300; letter-spacing: .01em; }
  .person__role { font-size: 11px; color: var(--ink-muted); line-height: 1.35; margin-top: 4px; }

  .divider { position: absolute; left: 56px; right: 70px; top: 168px; height: 2px; background: var(--rule); }

  .contacts {
    position: absolute; left: 34px; right: 30px; top: 312px;
    display: flex; justify-content: space-between; color: var(--ink-muted);
  }
  .contact { display: flex; align-items: flex-start; gap: 6px; font-size: 12px; line-height: 1.4; }
  .contact svg { width: 13px; height: 13px; margin-top: 2px; fill: none; stroke: var(--ink-light); stroke-width: 1.6; }
  .contact__bar { width: 2px; height: 15px; background: var(--ink-light); margin-top: 1px; }
</style>
</head>
<body>
<main class="stage">
  <section class="card card--back" aria-label="Kartenrückseite">
    <div class="wordmark">
      <span class="wordmark__name">Zelliger</span>
      <span class="wordmark__suffix">&amp; Partner mbB</span>
      <span class="wordmark__tagline">Steuerberater | Wirtschaftsprüfer</span>
    </div>
  </section>

  <section class="card card--front" aria-label="Kartenvorderseite">
    <div class="person">
      <p class="person__name">Anton R. Zelliger</p>
      <p class="person__role">Dipl.-Kfm / Steuerberater<br>Wirtschaftsprüfer</p>
    </div>
    <div class="divider"></div>
    <div class="wordmark">
      <span class="wordmark__name">Zelliger</span>
      <span class="wordmark__suffix">&amp; Partner mbB</span>
      <span class="wordmark__tagline">Steuerberater | Wirtschaftsprüfer</span>
    </div>
    <div class="contacts">
      <div class="contact">
        <svg viewBox="0 0 16 16" aria-hidden="true"><path d="M2 8 8 2.5 14 8M4 7v6.5h8V7"/></svg>
        <span class="contact__bar"></span>
        <p>Lindenhainstraße 22<br>80331 München</p>
      </div>
      <div class="contact">
        <svg viewBox="0 0 16 16" aria-hidden="true"><path d="M4 2.5 6 5 5 6.5c.8 1.8 2 3 3.6 3.7L10 9l2.5 2-1 2.5C7 13 3 9 2.5 4.5Z"/></svg>
        <span class="contact__bar"></span>
        <p>T 089 - 47 21 3080<br>F 089 - 47 21 3089</p>
      </div>
      <div class="contact">
        <svg viewBox="0 0 16 16" aria-hidden="true"><circle cx="8" cy="8" r="6"/><path d="M2 8h12M8 2c-3 3.5-3 8.5 0 12M8 2c3 3.5 3 8.5 0 12"/></svg>
        <span class="contact__bar"></span>
        <p>info@kanzlei-zelliger.com<br>www.kanzlei-zelliger.com</p>
      </div>
    </div>
  </section>
</main>
</body>
</html>
```